PeakRoamJourneys

1. Can you describe what your company does?

Please find enclosed documents for your reference about our business doing.

2. Who are your target customers for the website?

Company Positioning: A comprehensive supplier of premier international sports travel and high-end event services.
Core Advantage: Exclusive international partnership resources and an Official Ticketing Assurance System.
Service Standard: One-Stop, High-Quality Service Solutions based on the "An once-in-a-lifetime experience" philosophy.

Our target customers for the website:
Mid-to-High-end Sports Enthusiasts
Corporate Clients
Sports Associations
Please kindly find enclosed for more details about our target customers, I think it's very important to make it clear to you.

3. Do you have an existing domain name / website address?

Yes, I have. I just applied for this new domain and it's totally a new website. www.peakroamjourneys.example

4. In addition to a Home Page, which other pages / sections would you like your website to have:
About Us
Contact Us , Office / Mailing Address
Sports Travel Products( Bucket Lists) : Globe Shield, Royal Quartet, Vantara Games, Football, KHL, Golf, Skiing, Hiking,Galas
Reviews/ Unforgettable Moments
FAQs
Any other page / section you would like: Here is the website for your reference, www.lanewander.example
For each of the pages / sections you’d like to have, please provide the text (and images, if available) you would like to include.
Please recommend 2-3 templates to me, and let me know what kind of text I will provide to every web pages.

5. Which of the below are features and functionalities your website will need:
Image Gallery
Videos
Contact Form
Maps
FAQs
6. Please provide the URLs for the social media profiles you'd like to link to the website.

Do you know Bright Lantern App?

Please let me know anything you need, thank you very much!

Have a good day!

Target Market(s)

Travel for the world-wide sports games and make an once-in-a-lifetime experience

Industry/Entity Type

sports and travel industry

Coding

Number of Pages Required

5+ page

Requirements
Must have
• our logo
Nice to have
• On the homepage, I’d like a banner-style section to prominently showcase the latest products.

```html
<!DOCTYPE html>
<html lang="en">
<head>
<meta charset="utf-8">
<title>PeakRoamJourneys – The Ultimate in Sports Travel</title>
<link href="https://fonts.googleapis.com/css2?family=Montserrat:wght@400;500;600;700;800&display=swap" rel="stylesheet">
<style>
:root{
  --orange:#ff7a00;
  --ink:#1c1c1e;
  --text:#444;
  --teal:#2a7d9c;
  --teal-dark:#1d5f78;
  --link:#2a7d9c;
  --soft:#eef0f3;
  --news:#2b2c2f;
  --foot:#202124;
  --white:#fff;
}
*{box-sizing:border-box;margin:0;padding:0}
html,body{width:1200px;height:5042px;overflow:hidden}
body{font-family:"Montserrat",sans-serif;color:var(--ink);background:var(--white);position:relative}
section,header,footer{position:absolute;left:0;width:1200px}
.abs{position:absolute}
.photo{position:absolute;border-radius:14px}

/* header */
.site-header{top:0;height:82px;background:var(--white)}
.brand{left:74px;top:26px;font-size:27px;font-weight:700;color:var(--ink)}
.nav{right:73px;top:33px;display:flex;gap:38px;font-size:14px;font-weight:600}
.nav a{color:var(--ink);text-decoration:none}
.nav a.active{color:var(--orange)}

/* hero */
.hero{top:82px;height:638px;background:linear-gradient(100deg,#141a22 0%,#2a3a3e 45%,#3f5a3a 75%,#1d2b1f 100%)}
.hero-title{left:74px;top:145px;font-size:80px;line-height:92px;font-weight:800;color:var(--white)}
.hero-sub{left:74px;top:318px;font-size:44px;line-height:44px;font-weight:800;color:var(--white)}
.search{left:74px;top:433px;width:449px;height:49px;background:rgba(255,255,255,.88);border-radius:3px}
.search span{position:absolute;left:18px;top:16px;font-size:13px;font-weight:600;color:#222}
.search-btn{position:absolute;right:8px;top:8px;width:34px;height:34px;background:#111;border-radius:2px}

/* about */
.about{top:720px;height:533px}
.about h2{left:617px;top:84px;font-size:40px;font-weight:700}
.about p{position:absolute;left:617px;width:512px;font-size:14.5px;line-height:24px;color:var(--text)}
.btn{position:absolute;background:var(--orange);color:var(--white);font-weight:700;display:flex;align-items:center;justify-content:center}
.about .btn{left:617px;top:397px;width:162px;height:43px;font-size:16px}

/* products */
.products{top:1253px;height:495px;background:var(--teal)}
.products h2{left:72px;top:56px;font-size:40px;font-weight:700;color:var(--white)}
.arrow{position:absolute;width:20px;height:20px}
.card{top:131px;width:243px;height:286px;border-radius:14px;overflow:hidden}
.card .label{position:absolute;left:0;right:0;bottom:18px;text-align:center;color:var(--white);font-size:24px;font-weight:600}
.card::after{content:"";position:absolute;inset:0;background:linear-gradient(180deg,transparent 60%,rgba(0,0,0,.7))}
.card .label{z-index:1}

/* video */
.video{top:1748px;height:679px}
.section-title{width:1200px;text-align:center;font-size:42px;font-weight:700}
.video .section-title{top:62px}
.video-frame{left:74px;top:137px;width:1053px;height:462px;border-radius:14px;background:linear-gradient(100deg,#3a3a36 0%,#8a7a66 35%,#c7b19a 55%,#6b5a4a 80%,#2d2a28 100%)}
.play{position:absolute;left:486px;top:191px}

/* reviews */
.reviews{top:2427px;height:456px;background:var(--soft)}
.reviews h2{left:72px;top:54px;font-size:40px;font-weight:700}
.review{top:142px;width:336px}
.stars{display:flex;gap:5px}
.review p{margin-top:12px;font-size:14px;line-height:23px;color:var(--text)}
.review h3{margin-top:12px;font-size:16px;font-weight:700;color:var(--link)}
.outline-btn{left:495px;top:346px;width:208px;height:52px;border:1.5px solid #888;background:var(--white);font-size:15px;font-weight:700;display:flex;align-items:center;justify-content:center}

/* gallery */
.gallery{top:2883px;height:679px}
.gallery .section-title{top:66px}
.tile{width:341px;height:213px}

/* faq */
.faq{top:3562px;height:542px;background:linear-gradient(120deg,#1f6a86 0%,#2a7d9c 45%,#1c5c74 100%)}
.faq .section-title{top:78px;color:var(--white)}
.acc{left:74px;width:513px;height:50px;border-bottom:1px solid rgba(255,255,255,.55);color:var(--white);font-size:14px;font-weight:600;display:flex;align-items:center;justify-content:space-between;padding-right:12px}
.acc.open{background:#1f2a33;padding-left:20px;border:none}
.acc .sign{font-size:22px;font-weight:600}
.answer{left:615px;top:160px;width:512px;height:296px;background:var(--white);padding:22px 20px;font-size:14px;line-height:24px;color:var(--text)}

/* contact */
.contact{top:4104px;height:521px}
.contact h2{top:64px;font-size:40px;font-weight:700}
.field{width:241px;height:48px;border:1px solid #ccc;font-size:12px;font-weight:600;padding:17px 16px}
.map{left:617px;top:143px;width:510px;height:305px;border-radius:14px;background:linear-gradient(135deg,#dfe7d6 0%,#e9eee2 40%,#cfe0e6 70%,#e2e9dc 100%)}

/* newsletter */
.newsletter{top:4625px;height:156px;background:var(--news)}
.newsletter h2{left:74px;top:42px;font-size:22px;font-weight:700;color:var(--white)}
.newsletter p{left:74px;top:78px;width:500px;font-size:13px;line-height:20px;color:#aaa}
.email{left:617px;top:55px;width:508px;height:47px;background:var(--white);border-radius:3px}
.email span{position:absolute;left:14px;top:16px;font-size:12px;color:#333}
.email .btn{right:6px;top:6px;width:102px;height:35px;font-size:12px}

/* footer */
.site-footer{top:4781px;height:261px;background:var(--foot);color:var(--white)}
.fcol{top:28px}
.fcol h4{font-size:15px;font-weight:700;margin-bottom:8px}
.fcol li{list-style:none;font-size:12px;line-height:27px;color:#ddd}
.copy{left:74px;top:232px;font-size:10px;color:#ccc}
.social{right:70px;top:224px;display:flex;gap:14px;font-size:11px;font-weight:600;color:var(--white)}
</style>
</head>
<body>

<header class="site-header">
  <div class="abs brand">PeakRoamJourneys</div>
  <nav class="abs nav">
    <a class="active" href="#">Home</a><a href="#">About Us</a><a href="#">Products</a><a href="#">Reviews</a><a href="#">FAQ's</a><a href="#">Gallery</a><a href="#">Contact Us</a>
  </nav>
</header>

<section class="hero" role="img" aria-label="Footballer leaping for the ball in a floodlit stadium">
  <h1 class="abs hero-title">PeakRoam<br>Journeys</h1>
  <div class="abs hero-sub">The Ultimate in<br>Sports Travel</div>
  <div class="abs search"><span>Find your sport events</span>
    <div class="search-btn"><svg width="34" height="34" viewBox="0 0 34 34"><circle cx="15.5" cy="15.5" r="5.5" fill="none" stroke="#fff" stroke-width="2.2"/><line x1="19.5" y1="19.5" x2="24" y2="24" stroke="#fff" stroke-width="2.4"/></svg></div>
  </div>
</section>

<section class="about">
  <div class="photo" role="img" aria-label="Basketball player dunking, seen from above" style="left:74px;top:75px;width:400px;height:332px;background:linear-gradient(135deg,#b9b7b2,#8a8c8f 60%,#5b7c92)"></div>
  <div class="photo" role="img" aria-label="Jockey racing a horse" style="left:317px;top:192px;width:270px;height:262px;background:linear-gradient(160deg,#2c3440,#4a3a2e 60%,#1c1e22);border:3px solid #fff"></div>
  <h2 class="abs">About PeakRoamJourneys</h2>
  <p style="top:148px">Nemo enim ipsam voluptatem quia voluptas sit aspernatur aut odit aut fugit, sed quia consequuntur magni dolores eos qui ratione voluptatem sequi nesciunt. Neque porro quisquam est, qui dolorem ipsum quia dolor sit amet, consectetur, adipisci velit, sed quia non numquam eius modi tempora incidunt ut labore et dolore magnam aliquam quaerat voluptatem.</p>
  <p style="top:298px">Nemo enim ipsam voluptatem quia voluptas sit aspernatur aut odit aut fugit, sed quia consequuntur magni dolores eos qui ratione voluptatem sequi nesciunt.</p>
  <div class="btn">Read More</div>
</section>

<section class="products">
  <h2 class="abs">Sports Travel Products</h2>
  <svg class="arrow" style="left:1071px;top:68px" viewBox="0 0 20 20"><polyline points="13,3 6,10 13,17" fill="none" stroke="#fff" stroke-width="2.4"/></svg>
  <svg class="arrow" style="left:1108px;top:68px" viewBox="0 0 20 20"><polyline points="7,3 14,10 7,17" fill="none" stroke="#fff" stroke-width="2.4"/></svg>
  <div class="abs card" style="left:74px"><div class="photo" role="img" aria-label="Golden trophy in a stadium" style="inset:0;border-radius:0;background:linear-gradient(180deg,#1d3a6e,#3a6f9e 50%,#2f6a32)"></div><div class="label">Globe Shield</div></div>
  <div class="abs card" style="left:344px"><div class="photo" role="img" aria-label="Tennis player serving" style="inset:0;border-radius:0;background:linear-gradient(160deg,#3a2a1c,#a77a3e 55%,#e1a03a)"></div><div class="label">Royal Quartet</div></div>
  <div class="abs card" style="left:614px"><div class="photo" role="img" aria-label="Sprinters on a running track" style="inset:0;border-radius:0;background:linear-gradient(180deg,#6d7a5e,#9a7560 50%,#b8573d)"></div><div class="label">Vantara Games</div></div>
  <div class="abs card" style="left:884px"><div class="photo" role="img" aria-label="Football players on the pitch" style="inset:0;border-radius:0;background:linear-gradient(180deg,#3b4f6e,#2d5aa0 50%,#2c6a2f)"></div><div class="label">Football</div></div>
</section>

<section class="video">
  <h2 class="abs section-title">Watch Video</h2>
  <div class="abs video-frame" role="img" aria-label="Cheering crowd of fans in a stadium">
    <svg class="play" width="80" height="80" viewBox="0 0 80 80"><circle cx="40" cy="40" r="36" fill="none" stroke="#fff" stroke-width="5"/><polygon points="31,24 58,40 31,56" fill="#fff"/></svg>
  </div>
</section>

<section class="reviews">
  <h2 class="abs">Reviews</h2>
  <svg class="arrow" style="left:1071px;top:70px" viewBox="0 0 20 20"><polyline points="13,3 6,10 13,17" fill="none" stroke="#222" stroke-width="2.4"/></svg>
  <svg class="arrow" style="left:1108px;top:70px" viewBox="0 0 20 20"><polyline points="7,3 14,10 7,17" fill="none" stroke="#2a7d9c" stroke-width="2.4"/></svg>
  <div class="abs review" style="left:74px">
    <div class="stars"><svg width="94" height="16" viewBox="0 0 94 16"><g fill="#ff7a00"><polygon id="st" points="8,0 10.4,5.2 16,5.8 11.8,9.6 13,15.2 8,12.4 3,15.2 4.2,9.6 0,5.8 5.6,5.2"/><use href="#st" x="19"/><use href="#st" x="38"/><use href="#st" x="57"/><use href="#st" x="76"/></g></svg></div>
    <p>Duis aute irure dolor in reprehenderit in voluptate velit esse cillum dolore eu fugiat nulla pariatur sint occaecat cupidatat non proident..</p>
    <h3>Name Heading</h3>
  </div>
  <div class="abs review" style="left:436px">
    <div class="stars"><svg width="94" height="16" viewBox="0 0 94 16"><g fill="#ff7a00"><use href="#st"/><use href="#st" x="19"/><use href="#st" x="38"/><use href="#st" x="57"/><use href="#st" x="76"/></g></svg></div>
    <p>Duis aute irure dolor in reprehenderit in voluptate velit esse cillum dolore eu fugiat nulla pariatur sint occaecat cupidatat non proident..</p>
    <h3>Name Heading</h3>
  </div>
  <div class="abs review" style="left:798px">
    <div class="stars"><svg width="94" height="16" viewBox="0 0 94 16"><g fill="#ff7a00"><use href="#st"/><use href="#st" x="19"/><use href="#st" x="38"/><use href="#st" x="57"/><use href="#st" x="76"/></g></svg></div>
    <p>Duis aute irure dolor in reprehenderit in voluptate velit esse cillum dolore eu fugiat nulla pariatur sint occaecat cupidatat non proident..</p>
    <h3>Name Heading</h3>
  </div>
  <div class="abs outline-btn">View All Reviews</div>
</section>

<section class="gallery">
  <h2 class="abs section-title">Gallery</h2>
  <div class="photo tile" role="img" aria-label="Baseball player sliding into base" style="left:74px;top:156px;background:linear-gradient(180deg,#2b3550,#6a5a50 60%,#a56a44)"></div>
  <div class="photo tile" role="img" aria-label="Basketball player going for a dunk" style="left:430px;top:156px;background:linear-gradient(160deg,#1c1f22,#4a4a44 60%,#2a2a28)"></div>
  <div class="photo tile" role="img" aria-label="Fan with painted cheeks cheering" style="left:786px;top:156px;background:linear-gradient(140deg,#b33a3a,#e2c2b0 50%,#2d4a8a)"></div>
  <div class="photo tile" role="img" aria-label="Tennis player hitting a forehand" style="left:74px;top:386px;background:linear-gradient(180deg,#1e2a24,#3a3a3a 50%,#1a1c1e)"></div>
  <div class="photo tile" role="img" aria-label="Golfer swinging on a course" style="left:430px;top:386px;background:linear-gradient(180deg,#9cc7e0,#7aa2a0 55%,#5a8a3a)"></div>
  <div class="photo tile" role="img" aria-label="Footballers contesting the ball" style="left:786px;top:386px;background:linear-gradient(180deg,#3b4f6e,#2d5aa0 45%,#2e7a32)"></div>
</section>

<section class="faq">
  <h2 class="abs section-title">FAQ's</h2>
  <div class="abs acc open" style="top:164px"><span>Duis aute irure dolor in reprehenderit in voluptate velit?</span><span class="sign">−</span></div>
  <div class="abs acc" style="top:206px"><span>Esse cillum dolore eu fugiat nulla pariatur?</span><span class="sign">+</span></div>
  <div class="abs acc" style="top:258px"><span>Excepteur sint occaecat cupidatat non proident?</span><span class="sign">+</span></div>
  <div class="abs acc" style="top:310px"><span>Duis aute irure dolor in reprehenderit in voluptate velit?</span><span class="sign">+</span></div>
  <div class="abs acc" style="top:362px"><span>Esse cillum dolore eu fugiat nulla pariatur?</span><span class="sign">+</span></div>
  <div class="abs acc" style="top:414px;border-bottom:none"><span>Excepteur sint occaecat cupidatat non proident?</span><span class="sign">+</span></div>
  <div class="abs answer">Sed ut perspiciatis unde omnis iste natus error sit voluptatem accusantium doloremque laudantium, totam rem aperiam, eaque ipsa quae ab illo inventore veritatis et quasi architecto beatae vitae dicta sunt explicabo. Nemo enim ipsam voluptatem quia voluptas sit aspernatur aut odit aut fugit, sed quia consequuntur magni dolores eos qui ratione voluptatem sequi nesciunt. Neque porro quisquam est, qui dolorem ipsum quia dolor sit amet, consectetur, adipisci velit, sed quia non numquam eius modi tempora incidunt ut labore et dolore magnam aliquam quaerat voluptatem.</div>
</section>

<section class="contact">
  <h2 class="abs" style="left:74px">Contact Us</h2>
  <h2 class="abs" style="left:617px">Location Map</h2>
  <div class="abs field" style="left:74px;top:145px">Name</div>
  <div class="abs field" style="left:329px;top:145px">Name</div>
  <div class="abs field" style="left:74px;top:208px">Name</div>
  <div class="abs field" style="left:329px;top:208px">Name</div>
  <div class="abs field" style="left:74px;top:272px;width:496px;height:110px">Message</div>
  <div class="btn" style="left:74px;top:390px;width:241px;height:50px;font-size:15px">Submit Now</div>
  <div class="abs map" role="img" aria-label="Street map of the office location"></div>
</section>

<section class="newsletter">
  <h2 class="abs">Sign up now and stay informed!</h2>
  <p class="abs">Duis aute irure dolor in reprehenderit in voluptate velit esse cillum dolore eu fugiat nulla pariatur.</p>
  <div class="abs email"><span>Email Address</span><div class="btn">Subscribe</div></div>
</section>

<footer class="site-footer">
  <div class="abs fcol" style="left:74px"><h4>Quick Links</h4><ul><li>Home</li><li>About Us</li><li>Products</li><li>Reviews</li></ul></div>
  <div class="abs fcol" style="left:211px;top:54px"><ul><li>FAQ's</li><li>Gallery</li><li>Contact Us</li></ul></div>
  <div class="abs fcol" style="left:405px"><h4>Connect</h4><ul><li>Excepteur sint</li><li>Occaecat</li><li>Cupidatat non proiden</li><li>Sunt in culp</li><li>Qui officia</li></ul></div>
  <div class="abs fcol" style="left:681px"><h4>Discover</h4><ul><li>Excepteur sint</li><li>Occaecat</li><li>Cupidatat non proiden</li><li>Sunt in culp</li><li>Qui officia</li></ul></div>
  <div class="abs fcol" style="left:943px"><h4>About Us</h4><ul><li>Excepteur sint</li><li>Occaecat</li><li>Cupidatat non proiden</li><li>Sunt in culp</li><li>Qui officia</li></ul></div>
  <div class="abs copy">© 2025 Company Name .  All Rights Reserved.</div>
  <div class="abs social"><span>Facepage</span><span>Chirp</span><span>Picstream</span><span>Worknet</span><span>Viewtube</span></div>
</footer>

</body>
</html>
```